Bright Harbor, LLC Business Card Design

We need a product business card designed for a new company Bright Harbor, LLC. We make and resell waterless RV cleaner, polish and protectant. It cleans and protects in a simple spray and wipe step leaving the surface protected and conditioned to repel dust, dirt, water, smudges, bugs and fingerprints while preventing fogging. Safe on acrylic, plexiglas, lexan, plastic, rubber, painted surfaces, chrome, stainless, aluminum, vinyl, leather, glass.... This is an eco-friendly green product.

We want to play off the company name to tell the consumer that the product is easy to use and associate to the nostalgics 1950's in the USA... Thinking old travel trailer with hot rod truck pulling it as the graphic, maybe the husband cleaning the truck and the wife cleaning the trailer for a Bright Harbor surface.
Updates

Just posted our newly finished logo. Need to have "Cleaner and Protectant" added to the design as well. Thanks everyone that has submitted thus far, i am working to get comments on all.

If you need a different file format, please let me know. Thank you.

Most important info, is the logo, website and the words "Cleaner" or "Clean" along "Protectant" or "Protect" the remainder is of less importance. Highlight: www.brightharborwash.example Focus is on company brand for Brighter Harbor Cleaner product: However, need a section for the following contact info: Walt Ferris (xxx) xxx-xxxx email address Would like space for QR Code if possible.

Target Market(s)

Adults in the USA between ages of 35-75 that are actively involved in the Recreational Vehicle (RV), travel trailer, and hot rod lifestyle. We are targeting the RV marked of the high end travel, 5th wheel and bus RV market. Along with hot rods, automotive and motorcycle market.

Industry/Entity Type

Travel

Requirements
Must have
• Most important info, is the logo, website and the words "Cleaner" or "Clean" along "Protectant" or "Protect" the remainder is of less importance.

Highlight:
www.brightharborwash.example

Focus is on company brand for Brighter Harbor Cleaner product: However, need a section for the following contact info:

Walt Ferris
(xxx) xxx-xxxx
email address
Nice to have
• Would like a space for a QR Code.

```html
<!DOCTYPE html>
<html lang="en">
<head>
<meta charset="utf-8">
<title>Bright Harbor, LLC — Business Card</title>
<link rel="stylesheet" href="https://fonts.googleapis.com/css2?family=Exo+2:ital,wght@0,400;0,500;0,600;0,700;0,800;1,400&display=swap">
<style>
  :root{
    --bg:#e9eaec;
    --card-top:#ffffff;
    --card-fade:#dcdde0;
    --ink:#23252e;
    --name-blue:#2f5fa8;
    --title-grey:#4a4d55;
    --blue-deep:#2f47b5;
    --blue-light:#3fa6e6;
    --contact:#ffffff;
  }
  *{box-sizing:border-box;margin:0;padding:0}
  html,body{width:1200px;height:899px;overflow:hidden}
  body{background:var(--bg);font-family:"Exo 2",sans-serif;position:relative}
  .card{
    position:absolute;width:540px;height:310px;border-radius:26px;overflow:hidden;
    background:linear-gradient(160deg,var(--card-top) 0%,var(--card-top) 45%,var(--card-fade) 100%);
    box-shadow:0 6px 22px rgba(0,0,0,.16);
  }
  .card--front{left:40px;top:294px}
  .card--back{left:620px;top:294px}
  .card__waves{position:absolute;inset:0;width:100%;height:100%}
  .brand{position:absolute;white-space:nowrap;line-height:1}
  .brand__name{font-weight:800;color:var(--ink);letter-spacing:.5px;text-transform:uppercase}
  .brand__tagline{font-weight:600;color:var(--name-blue);text-transform:uppercase;letter-spacing:2.2px;margin-top:7px}
  .card--front .brand{left:26px;top:58px}
  .card--front .brand__name{font-size:31px}
  .card--front .brand__tagline{font-size:12px}
  .card--back .brand{left:0;right:0;top:118px;text-align:center}
  .card--back .brand__name{font-size:40px}
  .card--back .brand__tagline{font-size:15px;margin-top:10px}
  .holder{position:absolute;right:30px;top:42px;text-align:right}
  .holder__name{font-size:19px;font-weight:500;color:var(--name-blue);letter-spacing:1.5px;text-transform:uppercase}
  .holder__role{font-size:13px;font-style:italic;color:var(--title-grey);margin-top:2px}
  .contact{
    position:absolute;right:28px;top:166px;text-align:right;color:var(--contact);
    font-size:11px;line-height:1.3;
  }
  .contact__address{margin-bottom:6px}
  .contact__row{display:flex;justify-content:flex-end;align-items:center;gap:7px;height:17px}
  .contact__row--web{font-size:13px;font-weight:700;height:21px;margin-top:2px;letter-spacing:.2px}
  .contact__icon{width:11px;height:11px;flex:none}
</style>
</head>
<body>

<section class="card card--front" aria-label="Business card front">
  <svg class="card__waves" viewBox="0 0 540 310" preserveAspectRatio="none" aria-hidden="true">
    <defs>
      <linearGradient id="blueField" x1="0" y1="0" x2="1" y2="0">
        <stop offset="0" stop-color="#2f47b5"/>
        <stop offset="1" stop-color="#3fa6e6"/>
      </linearGradient>
      <linearGradient id="greyBand" x1="0" y1="0" x2="1" y2="0">
        <stop offset="0" stop-color="#2e3036"/>
        <stop offset=".5" stop-color="#7d7f85"/>
        <stop offset="1" stop-color="#c9cacd"/>
      </linearGradient>
    </defs>
    <g transform="translate(0,-16)">
      <path d="M0 150 C120 185 230 150 330 128 C410 112 480 112 540 118 L540 150 C460 142 390 150 320 168 C220 192 110 210 0 184 Z" fill="url(#greyBand)"/>
      <path d="M0 178 C110 206 220 190 320 164 C395 146 465 140 540 146 L540 158 C465 154 395 162 322 178 C220 202 110 218 0 196 Z" fill="#ffffff"/>
      <path d="M0 190 C110 214 220 198 322 174 C398 156 468 152 540 156 L540 326 L0 326 Z" fill="url(#blueField)"/>
    </g>
  </svg>

  <div class="brand">
    <div class="brand__name">Bright Harbor</div>
    <div class="brand__tagline">Cleaner and Protectant</div>
  </div>

  <div class="holder">
    <div class="holder__name">Walt Ferris</div>
    <div class="holder__role">Managing Director</div>
  </div>

  <div class="contact">
    <div class="contact__address">27 Harbor Lane Suite 4<br>Bayview Road BHC</div>
    <div class="contact__row">555 014 2780
      <svg class="contact__icon" viewBox="0 0 12 12"><path d="M2.5 1 L4.5 1 L5.2 3.6 L4 4.6 C4.7 6 6 7.3 7.4 8 L8.4 6.8 L11 7.5 L11 9.5 C11 10.3 10.3 11 9.5 11 C5 11 1 7 1 2.5 C1 1.7 1.7 1 2.5 1Z" fill="#fff"/></svg>
    </div>
    <div class="contact__row">555 014 2781
      <svg class="contact__icon" viewBox="0 0 12 12"><rect x="3" y="0.5" width="6" height="11" rx="1" fill="none" stroke="#fff" stroke-width="1.2"/><circle cx="6" cy="9.5" r=".7" fill="#fff"/></svg>
    </div>
    <div class="contact__row">555 014 2782
      <svg class="contact__icon" viewBox="0 0 12 12"><rect x="1" y="4" width="10" height="6" rx="1" fill="#fff"/><rect x="3" y="1" width="6" height="3" fill="#fff"/></svg>
    </div>
    <div class="contact__row">walt@brightharbor.example
      <svg class="contact__icon" viewBox="0 0 12 12"><rect x="0.8" y="2.5" width="10.4" height="7" rx=".8" fill="#fff"/><path d="M1 3 L6 7 L11 3" fill="none" stroke="#3fa6e6" stroke-width="1"/></svg>
    </div>
    <div class="contact__row contact__row--web">www.brightharborwash.example
      <svg class="contact__icon" viewBox="0 0 12 12"><circle cx="6" cy="6" r="5" fill="none" stroke="#fff" stroke-width="1.1"/><ellipse cx="6" cy="6" rx="2.2" ry="5" fill="none" stroke="#fff" stroke-width="1"/><path d="M1 6 H11" stroke="#fff" stroke-width="1"/></svg>
    </div>
  </div>
</section>

<section class="card card--back" aria-label="Business card back">
  <div class="brand">
    <div class="brand__name">Bright Harbor</div>
    <div class="brand__tagline">Cleaner and Protectant</div>
  </div>
</section>

</body>
</html>
```